Music Quizz Application

Hello,

I want a new design for my Blind test (music quizz) application on Korvex. You will find attached the images I want to replace. I need something with the same element (menu / song title) but with a different look!

Same, new icon, you have carte blanche to this one.

I am looking for something fresh…. I'm looking for something with a real artistic choice, contrast, colours, etc.

As a marketing screenshot, I want something classic, you'll find an example attached, feel free to innovate.

To sum-up :

- One new view for my App
- One new icon
- One marketing screenshot

screen resolution :
640×960
icon resolution :
1024x1024

Target Market(s)

15-30 years

Industry/Entity Type

Marketing

```html
<!DOCTYPE html>
<html lang="en">
<head>
<meta charset="utf-8">
<title>Sonaro – Home Menu</title>
<link rel="stylesheet" href="https://fonts.googleapis.com/css2?family=Ubuntu:wght@500;700&display=swap">
<style>
  :root {
    --status-bg: #000000;
    --status-text: #e8e8e8;
    --status-dim: #8a8a8a;
    --brand-ink: #1a1614;
    --brand-accent: #f6a81c;
    --menu-top: #3e3b38;
    --menu-bottom: #141210;
    --menu-edge: #0b0a09;
    --menu-text: #f4f2ee;
    --divider-dark: #0e0d0c;
    --divider-light: #5a5652;
  }
  * { margin: 0; padding: 0; box-sizing: border-box; }
  html, body { width: 800px; height: 1200px; overflow: hidden; background: #000; }
  .screen {
    position: relative;
    width: 800px;
    height: 1200px;
    overflow: hidden;
    font-family: "Ubuntu", sans-serif;
  }
  .backdrop {
    position: absolute;
    inset: 0;
    background:
      radial-gradient(ellipse 260px 300px at 400px 720px, rgba(255,255,255,0.98), rgba(255,255,255,0) 100%),
      radial-gradient(ellipse 220px 200px at 680px 160px, rgba(190,50,20,0.85), rgba(190,50,20,0) 100%),
      radial-gradient(ellipse 300px 260px at 620px 400px, rgba(255,200,40,0.9), rgba(255,200,40,0) 100%),
      radial-gradient(ellipse 200px 240px at 60px 360px, rgba(70,210,170,0.85), rgba(70,210,170,0) 100%),
      radial-gradient(ellipse 180px 200px at 60px 760px, rgba(120,230,200,0.8), rgba(120,230,200,0) 100%),
      radial-gradient(ellipse 260px 220px at 260px 150px, rgba(170,190,110,0.85), rgba(170,190,110,0) 100%),
      radial-gradient(ellipse 200px 200px at 760px 640px, rgba(255,160,60,0.7), rgba(255,160,60,0) 100%),
      linear-gradient(180deg, #2a2a1a 0%, #6a6040 30%, #b0a070 55%, #403024 80%, #0c0a08 100%);
  }
  .status-bar {
    position: absolute;
    top: 0; left: 0;
    width: 800px;
    height: 52px;
    background: var(--status-bg);
    color: var(--status-text);
    font-weight: 700;
    font-size: 29px;
    line-height: 1;
  }
  .status-bar .signal { position: absolute; left: 10px; top: 26px; }
  .status-bar .carrier { position: absolute; left: 65px; top: 12px; }
  .status-bar .network { position: absolute; left: 152px; top: 13px; font-size: 26px; }
  .status-bar .clock { position: absolute; left: 0; width: 800px; top: 12px; text-align: center; }
  .status-bar .charge { position: absolute; left: 654px; top: 12px; }
  .status-bar .battery { position: absolute; left: 740px; top: 16px; }
  .brand {
    position: absolute;
    left: 0;
    top: 248px;
    width: 800px;
    text-align: center;
  }
  .brand-dot {
    display: block;
    width: 340px;
    height: 340px;
    margin: 0 auto;
    border-radius: 50%;
    background: var(--brand-accent);
  }
  .brand-name {
    display: block;
    margin-top: 6px;
    font-size: 90px;
    font-weight: 500;
    line-height: 1;
    letter-spacing: -1px;
    color: var(--brand-ink);
  }
  .main-menu {
    position: absolute;
    left: 156px;
    top: 738px;
    width: 488px;
    height: 276px;
    border-radius: 5px;
    border: 2px solid var(--menu-edge);
    background: linear-gradient(180deg, var(--menu-top) 0%, #2a2725 45%, var(--menu-bottom) 100%);
    box-shadow: 0 4px 14px rgba(0,0,0,0.45), inset 0 1px 0 rgba(255,255,255,0.18);
    list-style: none;
  }
  .menu-item {
    position: absolute;
    left: 0;
    width: 100%;
    text-align: center;
    color: var(--menu-text);
    font-size: 23px;
    font-weight: 700;
    line-height: 1;
  }
  .menu-item.quick { top: 43px; }
  .menu-item.blind { top: 132px; }
  .menu-item.challenge { top: 216px; }
  .menu-divider {
    position: absolute;
    left: 61px;
    width: 364px;
    height: 2px;
    border-top: 1px solid var(--divider-dark);
    border-bottom: 1px solid var(--divider-light);
  }
  .menu-divider.first { top: 95px; }
  .menu-divider.second { top: 179px; }
</style>
</head>
<body>
<main class="screen">
  <div class="backdrop" role="img" aria-label="Soft blurred bokeh of green, yellow, orange and red stage lights around a bright white glow"></div>

  <header class="status-bar">
    <svg class="signal" width="50" height="10" viewBox="0 0 50 10" aria-hidden="true">
      <rect x="0" y="0" width="6" height="9" fill="var(--status-text)"/>
      <rect x="10" y="6" width="5" height="3" fill="var(--status-dim)"/>
      <rect x="19" y="6" width="5" height="3" fill="var(--status-dim)"/>
      <rect x="28" y="6" width="5" height="3" fill="var(--status-dim)"/>
      <rect x="37" y="6" width="5" height="3" fill="var(--status-dim)"/>
    </svg>
    <span class="carrier">Orlix</span>
    <span class="network">3G</span>
    <span class="clock">12:14</span>
    <span class="charge">89 %</span>
    <svg class="battery" width="52" height="26" viewBox="0 0 52 26" aria-hidden="true">
      <rect x="1.5" y="1.5" width="44" height="23" rx="3" fill="none" stroke="var(--status-text)" stroke-width="3"/>
      <rect x="47" y="8" width="4" height="10" fill="var(--status-text)"/>
      <rect x="5" y="5" width="37" height="16" fill="var(--status-text)"/>
      <path d="M27 6 L18 14 L24 14 L20 21 L30 12 L24 12 Z" fill="var(--status-bg)"/>
    </svg>
  </header>

  <div class="brand">
    <span class="brand-dot" aria-hidden="true"></span>
    <h1 class="brand-name">Sonaro</h1>
  </div>

  <nav>
    <ul class="main-menu">
      <li class="menu-item quick">Quick Game</li>
      <li class="menu-divider first" aria-hidden="true"></li>
      <li class="menu-item blind">Blind Test</li>
      <li class="menu-divider second" aria-hidden="true"></li>
      <li class="menu-item challenge">Challenge</li>
    </ul>
  </nav>
</main>
</body>
</html>
```